MRT Property - Business Cards

Looking for a business card & general letterhead, signage etc design for our new logo.

Colours:
000a20
0056a2
00b5ef
0088ce
68cef2

Fonts:
Poppins
Karla

Please keep look and feel of new brand - example in the zip package I sent.

```html
<!DOCTYPE html>
<html lang="en">
<head>
<meta charset="utf-8">
<title>MRT Property – Business Card</title>
<link rel="stylesheet" href="https://fonts.googleapis.com/css2?family=Open+Sans:wght@600;700&family=Poppins:wght@400;500;600&display=swap">
<style>
  :root {
    --ink: #000a20;
    --navy: #0056a2;
    --blue: #0088ce;
    --name-blue: #15618d;
    --name-teal: #4b9ea5;
    --logo-teal: #3f9a9c;
    --card: #ece7df;
    --card-edge: #f7f4ef;
    --page: #d6cec2;
  }
  * { margin: 0; padding: 0; box-sizing: border-box; }
  html, body { width: 1200px; height: 1046px; overflow: hidden; }
  body {
    background: var(--page);
    font-family: "Poppins", sans-serif;
    color: var(--ink);
    position: relative;
  }
  .card {
    position: absolute;
    left: 100px;
    top: 252px;
    width: 1000px;
    height: 543px;
    background: var(--card);
    border: 1px solid var(--card-edge);
    border-radius: 30px;
    overflow: hidden;
  }
  .band { position: absolute; inset: 0; width: 100%; height: 100%; }
  .brand {
    position: absolute;
    right: 50px;
    top: 100px;
    display: flex;
    align-items: center;
    gap: 18px;
  }
  .brand-dot {
    width: 46px; height: 46px;
    border-radius: 50%;
    background: var(--logo-teal);
  }
  .brand-name {
    font-family: "Poppins", sans-serif;
    font-weight: 600;
    font-size: 62px;
    line-height: 1;
    color: var(--navy);
    letter-spacing: -0.5px;
  }
  .name-bar {
    position: absolute;
    left: 2px; top: 308px;
    width: 24px; height: 70px;
    background: var(--name-blue);
  }
  .person-name {
    position: absolute;
    left: 36px; top: 298px;
    font-family: "Open Sans", sans-serif;
    font-size: 50px;
    line-height: 58px;
    letter-spacing: -0.5px;
  }
  .person-name .first { font-weight: 700; color: var(--name-blue); }
  .person-name .last { font-weight: 600; color: var(--name-teal); }
  .person-role {
    position: absolute;
    left: 37px; top: 350px;
    font-weight: 600;
    font-size: 22px;
    line-height: 28px;
    color: #22323f;
  }
  .contacts {
    position: absolute;
    left: 34px; top: 410px;
    list-style: none;
  }
  .contacts li {
    display: flex;
    align-items: center;
    height: 32.5px;
    font-size: 24.5px;
    letter-spacing: 0.2px;
    color: #1c2330;
  }
  .contacts svg { width: 23px; height: 23px; margin-right: 15px; flex: none; }
  .address {
    position: absolute;
    right: 38px; top: 427px;
    text-align: right;
    font-size: 23.5px;
    line-height: 29.5px;
    color: #1c2330;
  }
</style>
</head>
<body>
  <section class="card" aria-label="MRT Property business card">
    <svg class="band" viewBox="0 0 1000 543" aria-hidden="true">
      <defs>
        <linearGradient id="bandTop" x1="0" x2="1">
          <stop offset="0" stop-color="#2a7fb6"/>
          <stop offset="1" stop-color="#0a5f92"/>
        </linearGradient>
        <linearGradient id="bandBottom" x1="0" x2="1">
          <stop offset="0" stop-color="#0b4d86"/>
          <stop offset="0.7" stop-color="var(--navy)"/>
          <stop offset="1" stop-color="#0a4f8c"/>
        </linearGradient>
      </defs>
      <polygon points="0,0 636,0 593,35 0,35" fill="url(#bandTop)"/>
      <polygon points="543,521 1000,521 1000,543 523,543" fill="url(#bandBottom)"/>
    </svg>

    <div class="brand">
      <span class="brand-dot"></span>
      <span class="brand-name">MRT Property</span>
    </div>

    <div class="name-bar"></div>
    <h1 class="person-name"><span class="first">Callum</span> <span class="last">Reid</span></h1>
    <p class="person-role">Director</p>

    <ul class="contacts">
      <li>
        <svg viewBox="0 0 24 24" aria-hidden="true"><path fill="var(--name-blue)" d="M6.6 3.5l2.6 3.3c.4.5.3 1.1-.1 1.5L7.6 9.7c1 2.4 3.3 4.7 5.7 5.7l1.4-1.5c.4-.4 1-.5 1.5-.1l3.3 2.6c.5.4.5 1 .1 1.5l-1.7 1.9c-.6.6-1.5.8-2.3.5C9.3 18.1 5.9 14.7 3.7 8.4c-.3-.8-.1-1.7.5-2.3l1.9-1.7c.1-.1.3-.9.5-.9z"/><path fill="none" stroke="var(--name-teal)" stroke-width="1.6" stroke-linecap="round" d="M14 3.5a6.5 6.5 0 0 1 6.5 6.5M14 7a3 3 0 0 1 3 3"/></svg>
        +61 2 5550 1234
      </li>
      <li>
        <svg viewBox="0 0 24 24" aria-hidden="true"><circle cx="12" cy="12" r="10" fill="var(--name-blue)"/><path fill="var(--name-teal)" d="M6 6.5c2 .2 3 1.5 2.6 3-.4 1.3 1.2 1.8 1 3.3-.2 1.2-1.5 1.4-1.2 3.2L6.8 18A9 9 0 0 1 6 6.5zM14 4c1.6.6 1.2 2 2.6 2.4 1.3.4 2.2 1.4 2.3 2.6-1.4.2-2.6 1-2.4 2.6.2 1.4 1.8 2 1.5 3.6-.3 1.5-1.8 2.5-2.4 3.6-.9-1.3-.3-2.8-1.4-3.7-1-.9-2.4-1.6-2-3.2.4-1.4 2-1.6 1.8-3.2C13.8 6.4 13 5 14 4z"/></svg>
        www.mrtproperty.com.au
      </li>
      <li>
        <svg viewBox="0 0 24 24" aria-hidden="true"><path fill="var(--name-blue)" d="M2 10l10-7 10 7v11H2z"/><rect x="5" y="6" width="14" height="9" fill="#f4f1ec"/><path fill="var(--name-teal)" d="M2 10l10 7 10-7v11H2z"/><circle cx="12" cy="10.5" r="2.2" fill="none" stroke="var(--name-blue)" stroke-width="1.1"/></svg>
        info@mrtproperty.com.au
      </li>
    </ul>

    <address class="address" style="font-style:normal">
      Suite 4.12, Level 4<br>
      18 Harbourline Road<br>
      Riverside Park NSW 2199
    </address>
  </section>
</body>
</html>
```